Need to drive pregnant women to my 3d4d ultrasound studio where i provide 4d ultrasound with hyperalistic imaging and gender reveals

Industry/Entity Type

Healthcare

Font styles to use
Decorative
Script

Requirements
Must have
• My Company name Cielo de Nuestra Espera 4D. EVERYTHING HAS TO BE IN SPANISH
Nice to have
• SIMPLE AND NOT TOO BUSY
Should not have
• website

```html
<!DOCTYPE html>
<html lang="es">
<head>
<meta charset="utf-8">
<title>Cielo de Nuestra Espera 4D – Banner</title>
<link rel="stylesheet" href="https://fonts.googleapis.com/css2?family=Roboto:wght@700&family=Dancing+Script:wght@500&display=swap">
<style>
  :root {
    --backdrop: #a0a0a0;
    --banner-black: #000000;
    --banner-sheen: #3a3a3d;
    --banner-mid: #1c1c1e;
    --banner-shadow: rgba(0, 0, 0, 0.35);
    --text-white: #ffffff;
    --text-soft: #f2f2f2;
    --frame-line: #e9e4df;
    --scan-dark: #2a1405;
    --scan-mid: #8a4a16;
    --scan-light: #d98a3e;
    --skin-dark: #a9786a;
    --skin-mid: #dcb3a4;
    --skin-light: #f1d4c6;
  }
  html, body {
    margin: 0;
    padding: 0;
    width: 1200px;
    height: 600px;
    overflow: hidden;
    background: var(--backdrop);
  }
  .canvas {
    position: relative;
    width: 1200px;
    height: 600px;
    background: var(--backdrop);
  }
  .banner {
    position: absolute;
    left: 79px;
    top: 154px;
    width: 1044px;
    height: 305px;
    background: linear-gradient(90deg,
      var(--banner-black) 0%,
      var(--banner-mid) 22%,
      var(--banner-sheen) 44%,
      var(--banner-mid) 54%,
      var(--banner-black) 63%,
      var(--banner-black) 100%);
    box-shadow: 1px 2px 2px var(--banner-shadow);
    overflow: hidden;
  }
  .headline {
    position: absolute;
    left: 69px;
    top: 48px;
    margin: 0;
    font-family: "Roboto", Arial, sans-serif;
    font-weight: 700;
    font-size: 53px;
    line-height: 61px;
    letter-spacing: 0.2px;
    color: var(--text-white);
    text-transform: uppercase;
    white-space: nowrap;
  }
  .tagline {
    position: absolute;
    left: 69px;
    top: 180px;
    margin: 0;
    font-family: "Dancing Script", "Brush Script MT", cursive;
    font-weight: 500;
    font-size: 34px;
    line-height: 38px;
    color: var(--text-soft);
    white-space: nowrap;
  }
  .gallery {
    position: absolute;
    left: 636px;
    top: 26px;
    width: 374px;
    height: 246px;
    display: flex;
    border: 1px solid var(--frame-line);
    box-sizing: border-box;
  }
  .gallery-panel {
    flex: 1;
    height: 100%;
  }
  .gallery-panel + .gallery-panel {
    border-left: 1px solid var(--frame-line);
  }
  .panel-scan {
    background: radial-gradient(ellipse at 45% 55%,
      var(--scan-light) 0%,
      var(--scan-mid) 45%,
      var(--scan-dark) 100%);
  }
  .panel-newborn {
    background: radial-gradient(ellipse at 45% 50%,
      var(--skin-light) 0%,
      var(--skin-mid) 55%,
      var(--skin-dark) 100%);
  }
</style>
</head>
<body>
  <div class="canvas">
    <section class="banner">
      <h1 class="headline">Cielo de Nuestra<br>Espera 4D</h1>
      <p class="tagline">Ecografía 4D con imágenes hiperrealistas<br>y revelación del sexo de tu bebé</p>
      <div class="gallery">
        <div class="gallery-panel panel-scan" role="img" aria-label="Imagen de ecografía 4D en tonos ámbar de un bebé en el vientre"></div>
        <div class="gallery-panel panel-newborn" role="img" aria-label="Fotografía de un recién nacido dormido, para comparar con la ecografía"></div>
      </div>
    </section>
  </div>
</body>
</html>
```